Website Redesign - We Need Your Magic!

Hello we are looking for you to help us re-design a high end and professional website for a high-end private school.

Here is the current site: http://www.ferndalecrest.com/

NOTE THIS IS DESIGN ONLY, NO CODING :)

The image they want to portray is that of high quality sports and education, in a creative "un-stiff" way.

Menu Bar: Horizontal

Look and Feel:

Site Colors: Dark green and a Gold yellow (logos are attached)

This site will represent a school so the look must be clean, bold, and classy. The site must have a very clean user interface, with things easily recognizable. Think simple.

The site should be visually appealing! If you come to me with templates, or a ton of text you will be out.

This site should be outside the box, we do not want boring, we do not want status quo. This site should instill excitement, innovation, and athletics.

So the main points again are:

1. High-end and classy look, with creative feel
2. Simple and clear navigation style
3. To cover the Junior and High School - Ferndale Crest College Schools

Think outside the box. We look forward to seeing what you come up with!!

Thank you for helping us create an amazing site for the school!

Industry/Entity Type

School

```html
<!DOCTYPE html>
<html lang="en">
<head>
<meta charset="utf-8">
<title>Ferndale Crest College</title>
<link rel="stylesheet" href="https://fonts.googleapis.com/css2?family=Open+Sans:wght@400;600;700&display=swap">
<style>
:root{
  --green:#1b6a3a;
  --green-dark:#134f2b;
  --green-text:#2f7a3f;
  --gold:#a9b43a;
  --header:#1e1f1f;
  --page:#e4e4e4;
  --panel:#ffffff;
  --rule:#d9d9d9;
  --ink:#555;
  --ink-dark:#333;
  --footer:#0f2431;
  --footer-bottom:#0a1a24;
}
*{box-sizing:border-box;margin:0;padding:0}
html,body{width:1200px;height:900px;overflow:hidden}
body{position:relative;background:var(--page);font-family:"Open Sans",Arial,sans-serif;color:var(--ink);font-size:7px;line-height:1.35}
.abs{position:absolute}
.top-band{left:0;top:0;width:1200px;height:6px;background:var(--green)}
.header{left:0;top:6px;width:1200px;height:70px;background:var(--header)}
.brand{left:160px;top:16px;display:flex;align-items:center;gap:10px}
.brand-mark{width:34px;height:34px;border-radius:50%;background:var(--green)}
.brand-name{font-size:23px;line-height:1;font-weight:600;color:var(--gold);width:220px}
.call{right:163px;top:36px;font-size:12px;color:#4d6b22;letter-spacing:.3px}
.nav{left:0;top:76px;width:1200px;height:19px;background:var(--green)}
.nav ul{position:absolute;left:160px;top:0;display:flex;list-style:none;height:19px}
.nav li{color:#e9f2e4;font-size:8.5px;font-weight:600;line-height:19px;padding:0 18px;border-right:1px solid var(--green-dark)}
.nav-search{left:1005px;top:80px;width:22px;height:11px;background:var(--green-dark);border:1px solid #2d8a4f}
.hero-band{left:0;top:95px;width:1200px;height:198px;background:var(--header)}
.hero{left:160px;top:105px;width:880px;height:181px;background:linear-gradient(180deg,#8bc34a 0%,#6aa336 45%,#b98a78 70%,#4f6b88 100%)}
.arrow{top:186px;width:51px;height:22px;background:var(--green)}
.col{background:var(--panel);border-top:2px solid var(--green)}
.w-title{font-size:10px;font-weight:600;color:#2f4a3a;letter-spacing:.3px;padding:4px 18px;border-bottom:1px dashed var(--rule);height:19px}
.pic{background:linear-gradient(135deg,#6a7f86,#c7b5a8)}
.h-green{color:var(--green-text);font-size:9.5px;font-weight:600;line-height:1.2}
.meta{color:#999;font-size:6.5px}
.more{color:#aaa;font-size:6.5px}
input.field{border:1px solid #bbb;height:11px;width:370px;background:#fff}
.btn{background:var(--green);color:#fff;font-size:7.5px;font-weight:700;padding:2px 10px;display:inline-block;letter-spacing:.5px}
.count{display:flex;justify-content:center;align-items:flex-start;gap:2px}
.count-group{display:flex;flex-direction:column;align-items:center}
.count-digits{display:flex;gap:2px}
.count-digits span{width:10px;height:14px;background:#222;color:#fff;font-size:11px;font-weight:700;text-align:center;line-height:14px}
.count-group small{font-size:4.5px;color:#666;font-weight:700;margin-top:1px}
.count i{width:3px;color:#222;font-style:normal;font-size:11px;font-weight:700;line-height:14px}
.ev-date{color:var(--green-text);font-size:11px;font-weight:700;text-align:center;line-height:1}
.ev-date small{display:block;font-size:9px;font-weight:400}
.ev-title{color:var(--ink-dark);font-size:8px}
.footer{left:0;top:803px;width:1200px;height:83px;background:var(--footer);color:#8a9aa3}
.footer-bottom{left:0;top:886px;width:1200px;height:14px;background:var(--footer-bottom);color:#6d7c84;font-size:6.5px;padding:4px 160px}
.f-title{color:#d8dde0;font-size:8.5px;font-weight:600}
.social{width:30px;height:15px;border-radius:2px}
</style>
</head>
<body>
<div class="abs top-band"></div>
<header class="abs header"></header>
<div class="abs brand"><span class="brand-mark"></span><span class="brand-name">Ferndale Crest College</span></div>
<div class="abs call">Call : (+44) 555 018 2640</div>
<nav class="abs nav"><ul><li>Home</li><li>Blog</li><li>News</li><li>Courses</li><li>Events</li><li>Gallery</li><li>About Us</li><li>Contact Us</li></ul></nav>
<div class="abs nav-search"><svg width="20" height="9" viewBox="0 0 20 9"><circle cx="9" cy="4" r="2.4" fill="none" stroke="#fff" stroke-width="1"/><line x1="10.8" y1="5.8" x2="13" y2="8" stroke="#fff" stroke-width="1.2"/></svg></div>

<div class="abs hero-band"></div>
<div class="abs hero" role="img" aria-label="Group of students sitting on grass sharing a tablet"></div>
<div class="abs arrow" style="left:160px"><svg width="51" height="22"><path d="M27 6 L21 11 L27 16" fill="none" stroke="#fff" stroke-width="3"/></svg></div>
<div class="abs arrow" style="left:989px"><svg width="51" height="22"><path d="M24 6 L30 11 L24 16" fill="none" stroke="#fff" stroke-width="3"/></svg></div>

<section class="abs col" style="left:160px;top:301px;width:220px;height:147px">
  <div class="pic" style="height:62px;background:linear-gradient(90deg,#f2f2f2 0%,#e8e8e8 50%,#c25a68 70%,#f0f0f0 100%)" role="img" aria-label="Student holding folders in a bright room"></div>
  <div style="padding:3px 18px">
    <div class="h-green">Lorem Ipsum</div>
    <p>Lorem ipsum dolor sit amet, consectetur adipiscing elit. In at nunc quam, ac molestie nisi. Duis nisi elit, dignissim non volutpat nec adipiscing ac odio Lorem ipsum dolor sit amet, consectetur adipiscing elit. In at nunc quam, ac molestie nisi.Lorem ipsum dolor sit amet, consectetur adipiscing elit. In at nunc quam, ac molestie nisi. Duis nisi elit, dignissim non vol...</p>
  </div>
</section>
<section class="abs col" style="left:160px;top:457px;width:220px;height:123px">
  <div class="w-title">CAMPUS &amp; COMMUNITY</div>
  <div class="pic" style="margin:4px 18px 0;height:44px;background:linear-gradient(90deg,#3f5f8a,#c9b6a0,#7a5a3a)" role="img" aria-label="Students studying in a library"></div>
  <div style="padding:3px 18px">
    <div class="h-green">Schools Liaison Officer Diary Ashbury and St Rowan</div>
    <p style="margin-top:3px">Lorem ipsum dolor sit amet, consectetur adipiscing elit. In at nunc quam, ac molestie nisi. Duis nis...</p>
  </div>
</section>
<section class="abs col" style="left:160px;top:589px;width:220px;height:144px">
  <div class="w-title">QUICK LINKS</div>
  <div class="pic" style="margin:4px 18px 0;height:37px;background:linear-gradient(90deg,#8a9a7a,#d8d0c8,#6f8a9a)" role="img" aria-label="Students talking in a corridor"></div>
  <div style="padding:1px 18px">
    <div class="h-green" style="font-size:8.5px;font-weight:700">COLLEG &amp; DEPARTMENTS</div>
    <p style="margin-top:4px">Lorem Ipsum is simply dummy text of the printing and typesetting industry. Lorem Ipsum has been the industry's standard dummy text ever since the 1500s, Lorem Ipsum is simply dummy text of the printing and typesetting industry. Lorem Ipsum has been the industry's standard dummy text ever since the 1500s,</p>
  </div>
</section>

<section class="abs col" style="left:397px;top:301px;width:405px;height:110px">
  <div class="w-title">ADVANCE SEARCH</div>
  <div style="padding:4px 18px;font-size:8.5px;color:#444">
    <div>Search for:</div>
    <input class="field" style="margin-top:3px" aria-label="Search for">
    <div style="margin-top:6px">Search In:</div>
    <div style="margin-top:2px;width:370px;height:12px;border:1px solid #bbb;font-size:6.5px;color:#888;padding:1px 6px;position:relative">Courses<span style="position:absolute;right:1px;top:1px;width:14px;height:8px;background:#ddd;border:1px solid #999"></span></div>
    <div class="btn" style="margin-top:8px">SEARCH</div>
  </div>
</section>
<section class="abs col" style="left:397px;top:420px;width:405px;height:353px">
  <div class="w-title">LATEST NEWS</div>
  <div class="pic" style="margin:16px 18px 0;height:98px;border:3px solid var(--green);background:linear-gradient(90deg,#4f7a3a,#a4a88a 40%,#d97a9a 65%,#5c7a3a)" role="img" aria-label="Students walking outdoors on campus"></div>
  <div style="padding:3px 18px 0">
    <div class="h-green">Post Detail Both Left Sidebar</div>
    <div class="meta">January 1, 2014</div>
    <p>Lorem Ipsum is simply dummy text of the printing and typesetting industry. Lorem Ipsum has been... <span class="more">Read more</span></p>
  </div>
  <div style="position:absolute;left:18px;top:174px;width:370px">
    <div style="display:flex;gap:9px;height:53px"><div class="pic" style="width:124px;height:33px;flex:none;background:linear-gradient(90deg,#6fa34a,#9aa0b0)" role="img" aria-label="Students outdoors with laptops"></div><div style="flex:1"><div class="h-green">Post Detail Both Right Sidebar</div><div class="meta">January 1, 2014</div><p>Lorem Ipsum is simply dummy text of the printing and typesetting industry. Lorem Ipsum has been the industry's standard dummy text ever since the 1500s,.. <span class="more">Read more</span></p></div></div>
    <div style="display:flex;gap:9px;height:53px"><div class="pic" style="width:124px;height:33px;flex:none;background:linear-gradient(90deg,#eee,#b77a66,#ddd)" role="img" aria-label="Students gathered around a laptop"></div><div style="flex:1"><div class="h-green">Sed iaculis pulvinar sapien nec varius</div><div class="meta">January 1, 2014</div><p>Lorem Ipsum is simply dummy text of the printing and typesetting industry. Lorem Ipsum has been the industry's standard dummy text ever since the 1500s,.. <span class="more">Read more</span></p></div></div>
    <div style="display:flex;gap:9px;height:53px"><div class="pic" style="width:124px;height:33px;flex:none;background:linear-gradient(90deg,#f4f4f4,#a77a66,#e8e8e8)" role="img" aria-label="Smiling students in a group"></div><div style="flex:1"><div class="h-green">Post Detail Right Sidebar</div><div class="meta">January 1, 2014</div><p>Lorem Ipsum is simply dummy text of the printing and typesetting industry. Lorem Ipsum has been the industry's standard dummy text ever since the 1500s,.. <span class="more">Read more</span></p></div></div>
  </div>
  <div style="position:absolute;left:0;bottom:0;width:100%;height:16px;background:#f0f0f0;padding:3px 10px;font-size:7px;font-weight:600;color:#444"><svg width="10" height="7" style="vertical-align:middle"><ellipse cx="5" cy="3.5" rx="4.5" ry="3" fill="#555"/><circle cx="5" cy="3.5" r="1.3" fill="#fff"/></svg> Show All News</div>
</section>

<section class="abs col" style="left:819px;top:301px;width:221px;height:174px">
  <div class="w-title">UPCOMING EVENTS</div>
  <div style="background:#eee;padding:10px 10px 6px">
    <div class="h-green" style="text-align:center;font-size:8.5px">Fusce et ullamc...</div>
    <div class="count" style="margin-top:5px">
      <div class="count-group"><div class="count-digits"><span>1</span><span>0</span><span>2</span></div><small>DAYS</small></div><i>:</i>
      <div class="count-group"><div class="count-digits"><span>0</span><span>9</span></div><small>HOURS</small></div><i>:</i>
      <div class="count-group"><div class="count-digits"><span>3</span><span>0</span></div><small>MINS</small></div><i>:</i>
      <div class="count-group"><div class="count-digits"><span>1</span><span>2</span></div><small>SECS</small></div>
    </div>
    <div style="background:#fff;border:1px solid #ddd;margin-top:5px;display:flex;gap:10px;padding:4px 8px">
      <div class="ev-date">08<small>Nov</small></div>
      <div><div class="ev-title">Fusce et ullamcorper turpis</div><div class="meta">Nov 08, 12:00 am to 1:00 am</div></div></div>
  </div>
  <div style="display:flex;gap:14px;padding:4px 12px;border-bottom:1px dashed var(--rule)"><div class="ev-date">06<small>Dec</small></div><div><div class="ev-title">Lorem ipsum dol...</div><div class="meta">Dec 06, 12:00 am to 1:00 am</div></div></div>
  <div style="display:flex;gap:14px;padding:4px 12px"><div class="ev-date">07<small>Dec</small></div><div><div class="ev-title">Nunc gravida el...</div><div class="meta">Dec 07, 12:00 am to 1:00 am</div></div></div>
  <div style="position:absolute;left:0;bottom:0;width:100%;height:11px;background:#eee;padding:1px 10px;font-size:6.5px;font-weight:600;color:#444">&#9633;&nbsp; VIEW ALL EVENTS</div>
</section>
<section class="abs col" style="left:819px;top:485px;width:221px;height:122px">
  <div class="w-title">THIS WEEK IN PHOTOS</div>
  <div class="pic" style="margin:14px 0 0 18px;width:186px;height:58px;background:linear-gradient(90deg,#b07a5a,#d8c0b0,#7aa04a,#c88a70)" role="img" aria-label="Grid of recent campus photos"></div>
  <div style="position:absolute;left:0;bottom:0;width:100%;height:12px;background:#eee;padding:2px 10px;font-size:6.5px;font-weight:600;color:#444">&#9679;&nbsp; View Gallery</div>
</section>
<section class="abs col" style="left:819px;top:616px;width:221px;height:172px">
  <div class="w-title">FRIENDLINE</div>
  <div style="padding:12px 8px 0;display:flex;gap:6px">
    <div style="width:42px;height:20px;background:#2f3a2a"></div>
    <div><div style="font-size:7.5px;color:#333">Crestline Media</div><div style="background:#4a64a0;color:#fff;font-size:6.5px;font-weight:700;padding:0 4px;display:inline-block">Like</div></div>
  </div>
  <div style="padding:3px 8px;font-size:6.5px;color:#555">49,090 people like Crestline Media.</div>
  <div class="pic" style="margin:2px 0 0 8px;width:184px;height:86px;background:linear-gradient(135deg,#c99a80,#8a6a5a,#d8b09a,#7a8a6a)" role="img" aria-label="Grid of follower profile pictures"></div>
  <div style="padding:2px 8px;font-size:6px;color:#777">Friendline social plugin</div>
</section>

<footer class="abs footer">
  <div class="abs" style="left:160px;top:9px;width:200px">
    <div class="f-title">About Us</div>
    <p>Lorem Ipsum is simply dummy text of the printing and typesetting industry. Lorem Ipsum has been the industry's standard dummy text ever since the 1500s, Lorem Ipsum is simply dummy text of the printing and typesetting industry. Lorem Ipsum has been the industry's standard dummy text ever since the 1500s,</p>
  </div>
  <div class="abs" style="left:385px;top:9px">
    <div class="f-title">Follow Us</div>
    <div style="display:flex;gap:12px;margin-top:6px"><span class="social" style="background:#3aa0d8"></span><span class="social" style="background:#3b5a9a"></span><span class="social" style="background:#1f7ab8"></span><span class="social" style="background:#d44b3a"></span></div>
  </div>
  <div class="abs" style="left:595px;top:12px;width:210px">
    <div style="display:flex;align-items:center;gap:8px"><span style="width:22px;height:22px;border-radius:50%;background:var(--green)"></span><span style="font-size:11px;font-weight:600;color:var(--gold);line-height:1.1;width:110px">Ferndale Crest College</span></div>
    <p style="margin-top:6px">Lorem Ipsum is simply dummy text of the printing and typesetting industry. Lorem Ipsum has been the industry's standard dummy text ever since the 1500s,</p>
  </div>
  <div class="abs" style="left:833px;top:9px;width:207px">
    <div class="f-title">Sing Up For Newsletter</div>
    <p>Lorem Ipsum is simply dummy text of the printing and typesetting industry</p>
    <div style="margin-top:6px;height:11px;background:#fff;color:#888;font-size:6.5px;padding:1px 6px">Enter Email Address</div>
    <div class="btn" style="margin-top:3px">SUBMIT</div>
  </div>
</footer>
<div class="abs footer-bottom">Copyright 2014</div>
</body>
</html>
```